Project Overview: Website Redesign for Brovanta
We are looking to redesign our current website, www.brovantausa.example, to better match the style and functionality of these reference sites:
Quenrix Health
ZMD Hopwell
Key Requirements: Modern, Clean Design:
The site should have a professional and clean layout with clear messaging about our services.
Visual Elements: Use strong visuals like images, icons, or illustrations to support text and engage visitors.
Clear Service Breakdown: Easily digestible sections explaining what Brovanta offers, similar to the service explanations on the reference sites.
User-Friendly Navigation: Simple, intuitive navigation with visible CTAs (e.g., "Learn More," "Get Started").
Trust-Building Features: Incorporate trust elements like client logos, testimonials, or success stories to build credibility.
Mobile-Responsive:
Ensure the website is fully responsive and looks great on all devices (desktop, tablet, mobile).
SEO Optimization:
Deliverables: Fully functional website with modern design.
All content will be provided, but we may need help with imagery or layout recommendations.
Responsive design and mobile optimization.
We are looking for a clean, modern, and easy-to-navigate site that reflects the professionalism of our brand.

```html
<!DOCTYPE html>
<html lang="en">
<head>
<meta charset="utf-8">
<title>Brovanta — Medical Food for Sickle Cell Disease</title>
<link href="https://fonts.googleapis.com/css2?family=Urbanist:ital,wght@0,400;0,500;0,600;0,700;1,400&display=swap" rel="stylesheet">
<style>
:root{
  --red:#c0282e;
  --red-dark:#a51f25;
  --pink:#fbeef0;
  --pink-card:#f9e3e5;
  --grey-card:#ececec;
  --ink:#1c1c1c;
  --text:#3b3b3b;
  --footer:#1e1718;
  --white:#fff;
  --star:#f3b23a;
}
*{box-sizing:border-box;margin:0;padding:0}
html,body{width:1200px;height:4105px;overflow:hidden}
body{position:relative;background:var(--white);font-family:"Urbanist",Arial,sans-serif;color:var(--text)}
.abs{position:absolute}
.btn{position:absolute;display:flex;align-items:center;justify-content:center;background:var(--red);color:#fff;border-radius:20px;font-size:13px;font-weight:600;letter-spacing:.3px;text-transform:uppercase}
.sec-title{position:absolute;font-size:33px;font-weight:700;color:var(--ink);display:flex;align-items:center;gap:10px;letter-spacing:-.3px}
.sec-title em{font-style:normal;color:var(--red)}
.accent{width:22px;height:22px}

/* top bar */
.topbar{position:absolute;top:0;left:0;width:1200px;height:40px;font-size:11.5px;color:#555}
.topbar .item{position:absolute;top:10px;display:flex;align-items:center;gap:10px}
.topbar .ico{width:20px;height:20px;border:1.5px solid var(--red);border-radius:50%;display:flex;align-items:center;justify-content:center}

/* hero */
.hero-photo{position:absolute;top:72px;left:0;width:1200px;height:475px;border-radius:0 0 44px 44px;background:linear-gradient(100deg,#8d7a66 0%,#b49a83 30%,#d8cbbd 60%,#eee9e4 100%)}
.nav{position:absolute;top:43px;left:112px;width:977px;height:62px;background:var(--red);border-radius:6px;z-index:2}
.nav .logo{position:absolute;left:22px;top:9px;color:#fff;font-size:32px;font-weight:600;letter-spacing:.5px}
.nav .tag{position:absolute;left:24px;top:46px;color:#fff;font-size:6.5px;opacity:.9}
.nav ul{position:absolute;left:240px;top:20px;display:flex;gap:22px;list-style:none;color:#fff;font-size:11.5px;font-weight:600;text-transform:uppercase}
.nav li.active{background:#111;padding:4px 8px;border-radius:3px;margin-top:-4px}
.nav .search{position:absolute;right:22px;top:18px;width:26px;height:26px;background:rgba(255,255,255,.18);border-radius:4px;display:flex;align-items:center;justify-content:center}
.hero-text{position:absolute;top:166px;right:107px;text-align:right;font-size:25px;font-weight:600;line-height:44.5px;color:var(--ink);text-transform:uppercase}
.hero-text em{font-style:normal;color:var(--red)}
.hero-arrow{position:absolute;top:500px;width:24px;height:24px;border-radius:50%;display:flex;align-items:center;justify-content:center}

/* services */
.lead{position:absolute;font-size:15px;line-height:34px}
.svc{position:absolute;border-radius:6px;padding:20px 21px}
.svc h3{margin-top:78px;font-size:14px;font-weight:600;color:var(--red);text-transform:uppercase}
.svc p{margin-top:10px;font-size:13px;line-height:27px;color:#333}
.svc svg{position:absolute;top:18px;left:21px}
.svc.pink{background:var(--pink-card)}
.svc.grey{background:var(--grey-card)}
.svc.red{background:var(--red)}
.svc.red h3,.svc.red p{color:#fff}
.svc-photo{position:absolute;left:611px;top:862px;width:478px;height:214px;border-radius:6px;background:linear-gradient(90deg,#7c5a3e,#b08a64 45%,#d8c6ad 70%,#7f8f60)}
.pill{position:absolute;background:#fff;color:var(--red);border-radius:18px;font-size:12.5px;font-weight:600;display:flex;align-items:center;justify-content:center}

/* about */
.band{position:absolute;left:0;width:1200px;background:linear-gradient(135deg,#fbe9eb,#fdf5f6 50%,#f8e4e6);}
.about-photo{position:absolute;left:679px;top:1248px;width:324px;height:494px;border-radius:60px 14px 60px 14px;background:linear-gradient(160deg,#3a3432,#8c7466 45%,#c8b3a4 75%,#8a6c5a)}
.about-frame{position:absolute;left:672px;top:1242px;width:332px;height:502px;border:1.5px solid var(--red);border-radius:62px 16px 62px 16px}
.product{position:absolute;left:602px;top:1570px;width:176px;height:188px;background:linear-gradient(135deg,#ffffff,#e9e5e5 60%,#c9b6b7);border-radius:6px}
.hours{position:absolute;left:853px;top:1567px;width:221px;height:150px;background:var(--red);border-radius:8px;color:#fff;padding:22px 22px}
.hours h4{font-size:15px;font-weight:600;text-transform:uppercase}
.hours table{margin-top:14px;font-size:11px;font-weight:600;border-collapse:collapse}
.hours td{padding:3px 0;padding-right:20px}
.clock{position:absolute;left:1035px;top:1555px;width:60px;height:60px;border-radius:50%;background:#111;border:4px solid #fff;display:flex;align-items:center;justify-content:center}

/* clients */
.client{position:absolute;top:2016px;width:172px;height:136px;background:#f8f8f8;border-radius:4px;box-shadow:0 3px 6px rgba(0,0,0,.08);display:flex;flex-direction:column;align-items:center;justify-content:center;gap:10px;font-size:16px;font-weight:700;color:#2d2d2d;letter-spacing:.6px;text-transform:uppercase}
.client .mark{width:30px;height:30px;border-radius:50%;background:#2d2d2d}
.circ{position:absolute;top:2070px;width:28px;height:28px;border:1.5px solid #333;border-radius:50%;display:flex;align-items:center;justify-content:center}

/* offers */
.offer{position:absolute;top:2467px;width:306px;height:405px;background:#fff;border-radius:16px;border:1px solid #f0dfe0;padding:40px 27px}
.offer .head{display:flex;align-items:center;gap:18px;font-size:15px;font-weight:500;color:#222;text-transform:uppercase;line-height:30px}
.offer .ic{flex:none;width:44px;height:44px;border-radius:50%;background:var(--red);display:flex;align-items:center;justify-content:center}
.offer .arr{margin-left:auto}
.offer p{margin-top:14px;font-size:13.5px;line-height:30px;color:#444}
.offer .ph{margin-top:24px;width:251px;height:152px;border-radius:8px}

/* testimonials */
.testi{position:absolute;border-radius:20px;padding:30px 42px}
.testi.pink{background:var(--pink-card)}
.testi.grey{background:var(--grey-card)}
.testi .q{color:var(--red);font-size:58px;font-weight:700;line-height:40px;height:34px;font-family:Georgia,serif}
.testi p{font-style:italic;font-size:13.5px;line-height:29px;color:#444;margin-top:16px}
.person{position:absolute;left:40px;display:flex;align-items:center;gap:20px}
.avatar{width:50px;height:50px;border-radius:50%;background:linear-gradient(135deg,#d9d0cc,#8e8783);border:2px solid #fff}
.person b{display:block;font-size:12.5px;font-weight:600;color:#222;text-transform:uppercase}
.person span{display:block;font-size:12.5px;color:var(--red);text-transform:uppercase;margin-top:6px}
.stars{position:absolute;color:var(--star);font-size:15px;letter-spacing:4px}
.testi.small{padding:22px 30px}
.testi.small .q{font-size:48px}
.testi.small p{font-size:12px;line-height:27px;margin-top:10px}
.testi.small .person{left:28px;gap:16px}
.testi.small .avatar{width:42px;height:42px}
.testi.small .person b,.testi.small .person span{font-size:11.5px}

/* footer */
.footer{position:absolute;top:3822px;left:0;width:1200px;height:283px;background:var(--footer);color:#fff;text-align:center}
.footer .flogo{position:absolute;top:50px;width:100%;font-size:54px;font-weight:600;letter-spacing:1px}
.footer .ftag{position:absolute;top:112px;width:100%;font-size:9px}
.footer nav{position:absolute;top:167px;width:100%;font-size:15px;display:flex;justify-content:center;gap:20px}
.footer .copy{position:absolute;top:223px;width:100%;font-size:15px}
</style>
</head>
<body>

<!-- top contact bar -->
<div class="topbar">
  <div class="item" style="left:157px"><span class="ico"><svg width="10" height="10" viewBox="0 0 24 24"><path d="M6 2l4 5-2 3a12 12 0 0 0 6 6l3-2 5 4-3 4C10 22 2 14 2 5z" fill="none" stroke="#c0282e" stroke-width="2"/></svg></span>+1 555 014 2291</div>
  <div class="item" style="left:467px"><span class="ico"><svg width="10" height="10" viewBox="0 0 24 24"><rect x="3" y="6" width="18" height="12" fill="none" stroke="#c0282e" stroke-width="2"/><path d="M3 6l9 7 9-7" fill="none" stroke="#c0282e" stroke-width="2"/></svg></span>INFO@BROVANTA.EXAMPLE</div>
  <div class="item" style="left:797px"><span class="ico"><svg width="10" height="10" viewBox="0 0 24 24"><path d="M12 22s7-7 7-12a7 7 0 0 0-14 0c0 5 7 12 7 12z" fill="none" stroke="#c0282e" stroke-width="2"/><circle cx="12" cy="10" r="2.5" fill="#c0282e"/></svg></span>23, BROVANTA LOREM LIPSUM 789 345</div>
</div>

<!-- hero -->
<div class="hero-photo" role="img" aria-label="Mother hugging her young son on a sofa, teddy bear beside them"></div>
<header class="nav">
  <div class="logo">Brovanta</div>
  <div class="tag">(emulsified-docosahexaenoic acid triglyceride, eDHAtg)</div>
  <ul>
    <li class="active">Home</li><li>About Brovanta</li><li>SCD</li><li>Healthcare Professionals</li><li>Patient Support</li><li>Kestrel Sciences</li>
  </ul>
  <div class="search"><svg width="12" height="12" viewBox="0 0 24 24"><circle cx="10" cy="10" r="6" fill="none" stroke="#fff" stroke-width="3"/><path d="M15 15l6 6" stroke="#fff" stroke-width="3"/></svg></div>
</header>
<h1 class="hero-text">A medical food for<br>the <em>dietary management</em><br>of sickle cell disease in<br>pediatric and adult<br>patients.</h1>
<div class="btn" style="left:969px;top:402px;width:124px;height:33px">Get Started</div>
<div class="hero-arrow" style="left:1091px;background:#111"><svg width="10" height="10" viewBox="0 0 10 10"><path d="M6.5 1.5L3 5l3.5 3.5" stroke="#fff" stroke-width="1.8" fill="none"/></svg></div>
<div class="hero-arrow" style="left:1134px;background:var(--red)"><svg width="10" height="10" viewBox="0 0 10 10"><path d="M3.5 1.5L7 5 3.5 8.5" stroke="#fff" stroke-width="1.8" fill="none"/></svg></div>

<!-- services -->
<h2 class="sec-title" style="left:112px;top:648px">OUR <em>SERVICES</em><svg class="accent" viewBox="0 0 24 24"><path d="M5 20L19 6M12 5l7 1 1 7" stroke="#c0282e" stroke-width="2" fill="none"/></svg></h2>
<p class="lead" style="left:112px;top:704px;width:380px">Lorem ipsum dolor sit amet, consectetur adipiscing elit, sed do eiusmod tempor incididunt ut labore et dolore magna aliqua.</p>

<div class="svc pink" style="left:606px;top:633px;width:234px;height:213px">
  <svg width="52" height="52" viewBox="0 0 52 52" fill="none" stroke="#c0282e" stroke-width="2"><circle cx="26" cy="20" r="10"/><path d="M26 6v4M26 30v4M12 20h4M36 20h4"/><rect x="16" y="32" width="20" height="14" rx="3"/></svg>
  <h3>Strategic Consulting</h3>
  <p>Lorem ipsum dolor sit amet, consectetur adipiscing elit, sed do eiusmod tempor</p>
</div>
<div class="svc grey" style="left:854px;top:633px;width:235px;height:213px">
  <svg width="52" height="52" viewBox="0 0 52 52" fill="none" stroke="#333" stroke-width="2"><circle cx="16" cy="16" r="6"/><path d="M6 36c0-7 5-11 10-11s10 4 10 11"/><path d="M30 30l8-8 6 4 6-10" stroke="#c0282e"/><circle cx="34" cy="40" r="7"/></svg>
  <h3>Business Development</h3>
  <p>Lorem ipsum dolor sit amet, consectetur adipiscing elit, sed do eiusmod tempor</p>
</div>
<div class="svc grey" style="left:112px;top:862px;width:234px;height:214px">
  <svg width="56" height="48" viewBox="0 0 56 48" fill="none" stroke="#c0282e" stroke-width="2"><rect x="2" y="4" width="40" height="28" rx="2"/><path d="M14 40h16M22 32v8M8 26V18M16 26V12M24 26V16M32 26V10"/><path d="M44 6h10M44 12h8M44 18h10" stroke="#333"/></svg>
  <h3>Digital Transformation</h3>
  <p>Lorem ipsum dolor sit amet, consectetur adipiscing elit, sed do eiusmod tempor</p>
</div>
<div class="svc red" style="left:362px;top:862px;width:234px;height:214px">
  <svg width="60" height="50" viewBox="0 0 60 50" fill="none" stroke="#fff" stroke-width="2"><path d="M4 46V30h8v16M16 46V22h8v24M28 46V26h8v20"/><path d="M6 20l12-10 8 6 14-12"/><circle cx="48" cy="34" r="7"/><path d="M48 23v4M48 41v4M37 34h4M55 34h4"/></svg>
  <h3>Operational Efficiency</h3>
  <p>Lorem ipsum dolor sit amet, consectetur adipiscing elit, sed do eiusmod tempor</p>
</div>
<div class="svc-photo" role="img" aria-label="Mother and children preparing food together in a home kitchen"></div>
<div class="pill" style="left:637px;top:1023px;width:150px;height:33px">VIEW ALL SERVICES</div>

<!-- about -->
<div class="band" style="top:1162px;height:684px;border-radius:70px 0 70px 0"></div>
<h2 class="sec-title" style="left:112px;top:1232px">ABOUT <em>BROVANTA</em><svg class="accent" viewBox="0 0 24 24"><path d="M5 20L19 6M12 5l7 1 1 7" stroke="#c0282e" stroke-width="2" fill="none"/></svg></h2>
<p class="lead" style="left:112px;top:1291px;width:448px">BROVANTA is a medical food specifically formulated to provide a consistent and highly bioavailable form of DHA, a major fatty acid found in Omega-3 fish oil, to replenish what is damaged by the hemoglobin mutation (HbS) found in sickle cell disease patients. In clinical trials (2,3) conducted under a US Investigational New Drug Application, patients who consume high levels of DHA and see a significant increase in DHA blood levels. An increase in DHA levels may impact the oxidative and inflammatory cascade leading to sickle cell pain crises or vaso-occlusive events. BROVANTA was designed to provide this fatty acid used in these trials, in a safe, good tasting, easy to administer oral formulation.</p>
<div class="btn" style="left:112px;top:1731px;width:130px;height:37px">Learn More</div>
<svg class="abs" style="left:662px;top:1230px" width="64" height="64" viewBox="0 0 64 64"><g fill="#555"><circle cx="2" cy="2" r="1.3"/><circle cx="12" cy="2" r="1.3"/><circle cx="22" cy="2" r="1.3"/><circle cx="32" cy="2" r="1.3"/><circle cx="42" cy="2" r="1.3"/><circle cx="52" cy="2" r="1.3"/><circle cx="62" cy="2" r="1.3"/><circle cx="2" cy="12" r="1.3"/><circle cx="12" cy="12" r="1.3"/><circle cx="22" cy="12" r="1.3"/><circle cx="32" cy="12" r="1.3"/><circle cx="42" cy="12" r="1.3"/><circle cx="2" cy="22" r="1.3"/><circle cx="12" cy="22" r="1.3"/><circle cx="22" cy="22" r="1.3"/><circle cx="2" cy="32" r="1.3"/><circle cx="12" cy="32" r="1.3"/><circle cx="2" cy="42" r="1.3"/><circle cx="2" cy="52" r="1.3"/></g></svg>
<div class="about-frame"></div>
<div class="about-photo" role="img" aria-label="Family in a kitchen, father feeding a toddler while mother cooks with the children"></div>
<div class="product" role="img" aria-label="Brovanta product carton"></div>
<div class="hours">
  <h4>Working Hours:</h4>
  <table>
    <tr><td>MON TO FRI</td><td>09:30 - 07:30</td></tr>
    <tr><td>SATURDAY</td><td>10:30 - 5:00</td></tr>
    <tr><td>SUNDAY</td><td>CLOSED</td></tr>
  </table>
</div>
<div class="clock"><svg width="34" height="34" viewBox="0 0 34 34"><circle cx="17" cy="17" r="14" fill="none" stroke="#fff" stroke-width="2.5"/><path d="M17 9v8l5 4" stroke="#fff" stroke-width="2.5" fill="none"/></svg></div>

<!-- client logos -->
<h2 class="sec-title" style="left:470px;top:1925px">CLIENT <em>LOGOS</em><svg class="accent" viewBox="0 0 24 24"><path d="M5 20L19 6M12 5l7 1 1 7" stroke="#c0282e" stroke-width="2" fill="none"/></svg></h2>
<div class="circ" style="left:48px"><svg width="14" height="14" viewBox="0 0 14 14"><path d="M12 7H2M6 3L2 7l4 4" stroke="#333" stroke-width="1.6" fill="none"/></svg></div>
<div class="client" style="left:124px"><span class="mark"></span>Corvane</div>
<div class="client" style="left:319px"><span class="mark"></span>Fitmora</div>
<div class="client" style="left:513px"><span class="mark"></span>Nutrelle</div>
<div class="client" style="left:708px"><span class="mark"></span>Healvio</div>
<div class="client" style="left:902px"><span class="mark"></span>Urbanek</div>
<div class="circ" style="left:1119px"><svg width="14" height="14" viewBox="0 0 14 14"><path d="M2 7h10M8 3l4 4-4 4" stroke="#333" stroke-width="1.6" fill="none"/></svg></div>

<!-- offers -->
<div class="band" style="top:2235px;height:773px;border-radius:60px 60px 60px 60px"></div>
<h2 class="sec-title" style="left:399px;top:2292px">WHAT <em>BROVANTA OFFERS</em><svg class="accent" viewBox="0 0 24 24"><path d="M5 20L19 6M12 5l7 1 1 7" stroke="#c0282e" stroke-width="2" fill="none"/></svg></h2>
<p class="abs" style="left:120px;top:2358px;width:960px;text-align:center;font-size:15.5px;line-height:35px;color:#333">Lorem ipsum dolor sit amet, consectetur adipiscing elit, sed do eiusmod tempor incididunt ut labore et dolore magna aliqua<br>ad minim veniam quis nostrud exercitation ullamco laboris nisi ut aliquip ex ea commodo consequat.</p>

<div class="offer" style="left:116px">
  <div class="head"><span class="ic"><svg width="22" height="22" viewBox="0 0 24 24" fill="none" stroke="#fff" stroke-width="2"><rect x="5" y="3" width="14" height="18" rx="2"/><path d="M9 8h6M9 12h6M9 16h4"/></svg></span>Healthcare IT<br>Solutions<svg class="arr" width="14" height="14" viewBox="0 0 14 14"><path d="M1 7h11M8 3l4 4-4 4" stroke="#c0282e" stroke-width="1.8" fill="none"/></svg></div>
  <p>Lorem ipsuam dolor sit amet, consectetur adipiscing elit, sed do eiusmod tempor</p>
  <div class="ph" role="img" aria-label="Hands on a laptop with a network of people icons overlaid" style="background:linear-gradient(135deg,#1f3350,#4f6f92 55%,#9fb4cc)"></div>
</div>
<div class="offer" style="left:448px">
  <div class="head"><span class="ic"><svg width="22" height="22" viewBox="0 0 24 24" fill="none" stroke="#fff" stroke-width="2"><circle cx="8" cy="8" r="3"/><circle cx="16" cy="8" r="3"/><path d="M3 20c0-4 2-6 5-6s5 2 5 6M11 20c0-4 2-6 5-6s5 2 5 6"/></svg></span>Consulting<br>Services<svg class="arr" width="14" height="14" viewBox="0 0 14 14"><path d="M1 7h11M8 3l4 4-4 4" stroke="#c0282e" stroke-width="1.8" fill="none"/></svg></div>
  <p>Lorem ipsuam dolor sit amet, consectetur adipiscing elit, sed do eiusmod tempor</p>
  <div class="ph" role="img" aria-label="Two colleagues reviewing work on a laptop" style="background:linear-gradient(135deg,#6b5d4f,#b5a18c 50%,#dcd2c7)"></div>
</div>
<div class="offer" style="left:778px">
  <div class="head"><span class="ic"><svg width="22" height="22" viewBox="0 0 24 24" fill="none" stroke="#fff" stroke-width="2"><rect x="3" y="4" width="18" height="14" rx="2"/><rect x="9" y="10" width="6" height="5"/><path d="M10 10V8a2 2 0 0 1 4 0v2"/></svg></span>Data Security<svg class="arr" width="14" height="14" viewBox="0 0 14 14"><path d="M1 7h11M8 3l4 4-4 4" stroke="#c0282e" stroke-width="1.8" fill="none"/></svg></div>
  <p>Lorem ipsuam dolor sit amet, consectetur adipiscing elit, sed do eiusmod tempor</p>
  <div class="ph" role="img" aria-label="Person working with glowing security data overlays" style="background:linear-gradient(135deg,#cfe3f4,#5e95c9 50%,#1f4f86)"></div>
</div>
<div class="btn" style="left:512px;top:2914px;width:175px;height:37px">View More Offers</div>

<!-- testimonials -->
<h2 class="sec-title" style="left:428px;top:3079px">OUR <em>TESTIMONIALS</em><svg class="accent" viewBox="0 0 24 24"><path d="M5 20L19 6M12 5l7 1 1 7" stroke="#c0282e" stroke-width="2" fill="none"/></svg></h2>

<div class="testi pink" style="left:112px;top:3177px;width:475px;height:271px">
  <div class="q">“</div>
  <p>"Brovanta's team helped us transform our operations and navigate some of our toughest challenges. Their expertise in strategic planning and process optimization led to a 20% increase in our operational efficiency...</p>
  <div class="person" style="top:211px"><div class="avatar"></div><div><b>Daniel Hartwell</b><span>CEO of Brovanta</span></div></div>
  <div class="stars" style="left:352px;top:222px">★★★★★</div>
</div>
<div class="testi grey" style="left:611px;top:3177px;width:478px;height:271px">
  <div class="q">“</div>
  <p>"The Brovanta team provided invaluable insights that helped us expand into new markets. Their thorough market research and tailored business development strategies gave us a clear edge over our competitors. The results were impressive...</p>
  <div class="person" style="top:211px"><div class="avatar"></div><div><b>Owen Castellane</b><span>Marketing Director at Brovanta</span></div></div>
  <div class="stars" style="left:352px;top:222px">★★★★★</div>
</div>

<div class="testi pink small" style="left:112px;top:3472px;width:307px;height:186px">
  <div class="q">“</div>
  <p>"Brovanta's team helped us transform our operations and navigate...</p>
  <div class="person" style="top:125px"><div class="avatar"></div><div><b>Marcus</b><span>Founder</span></div></div>
  <div class="stars" style="left:190px;top:135px;font-size:13px;letter-spacing:3px">★★★★★</div>
</div>
<div class="testi pink small" style="left:445px;top:3472px;width:309px;height:186px">
  <div class="q">“</div>
  <p>"Brovanta's teLorem ipsum dolor sit amet, consectetur adipiscing elit...</p>
  <div class="person" style="top:125px"><div class="avatar"></div><div><b>Renata</b><span>Clients</span></div></div>
  <div class="stars" style="left:192px;top:135px;font-size:13px;letter-spacing:3px">★★★★★</div>
</div>
<div class="testi pink small" style="left:778px;top:3472px;width:311px;height:186px">
  <div class="q">“</div>
  <p>"Brovanta's approach to improving operational efficiency was exactly...</p>
  <div class="person" style="top:125px"><div class="avatar"></div><div><b>Selene</b><span>Manager</span></div></div>
  <div class="stars" style="left:192px;top:135px;font-size:13px;letter-spacing:3px">★★★★★</div>
</div>
<div class="btn" style="left:486px;top:3701px;width:225px;height:37px">View More Testimonials</div>

<!-- footer -->
<footer class="footer">
  <div class="flogo">Brovanta</div>
  <div class="ftag">(emulsified-docosahexaenoic acid triglyceride, eDHAtg)</div>
  <nav><span>Home</span><span>|</span><span>About BROVANTA</span><span>|</span><span>About SCD</span><span>|</span><span>Healthcare Professionals</span><span>|</span><span>Patient Support</span><span>|</span><span>Kestrel Sciences</span></nav>
  <div class="copy">© 2025 - All rights reserved</div>
</footer>

</body>
</html>
```